Investor Slide Deck

Simple idea - take a model investor deck and build out a investor deck for K7V. I will complete the data, I need a template to work from within. I will attach a model investor deck and a blank K7V that I need built out to K7V. Use the K7V Pwrpt to build out the investor deck

```html
<!DOCTYPE html>
<html lang="en">
<head>
<meta charset="utf-8">
<title>K7V Investor Deck Template</title>
<link href="https://fonts.googleapis.com/css2?family=Barlow+Semi+Condensed:wght@400;500;600;700&family=Barlow:wght@400;500;600&display=swap" rel="stylesheet">
<style>
:root{
  --page:#05272f;
  --ink:#1d1d1f;
  --body:#3a3a3a;
  --muted:#8a8a8a;
  --magenta:#ae1357;
  --teal:#0fa89c;
  --orange:#ff5a0a;
  --navy:#1f3f47;
  --blue:#1f6e8c;
  --yellow:#f6bf2e;
  --ochre:#d99f00;
  --panel:#f2f2f2;
  --mint:#d9f1ef;
  --cream:#fdf1d3;
  --peach:#fde3d8;
}
html,body{margin:0;padding:0;width:700px;height:1200px;overflow:hidden;background:var(--page)}
.deck{position:relative;width:700px;height:1200px;background:var(--page);overflow:hidden}
.slide{position:absolute;width:219px;height:123px;background:#fff;overflow:hidden}
.slide svg{display:block;width:100%;height:100%}
.col-1{left:15px}.col-2{left:240.5px}.col-3{left:466px}
.row-1{top:79.5px}.row-2{top:211px}.row-3{top:342px}.row-4{top:473px}
.row-5{top:604px}.row-6{top:735px}.row-7{top:866px}.row-8{top:997px}
.title{font-family:"Barlow Semi Condensed",sans-serif;font-weight:600;font-size:16px;fill:var(--ink)}
.head{font-family:"Barlow Semi Condensed",sans-serif;font-weight:600;font-size:8px;fill:var(--teal)}
.head-sm{font-family:"Barlow Semi Condensed",sans-serif;font-weight:600;font-size:6px;fill:var(--teal)}
.copy{font-family:"Barlow",sans-serif;font-size:5.6px;fill:var(--body)}
.fine{font-family:"Barlow",sans-serif;font-size:3.8px;fill:var(--body)}
.fine-w{font-family:"Barlow",sans-serif;font-size:3.8px;fill:#fff}
.label{font-family:"Barlow",sans-serif;font-size:4px;fill:var(--muted)}
.brand{font-family:"Barlow Semi Condensed",sans-serif;font-weight:700;font-size:7px;fill:#fff;letter-spacing:.4px}
.num{font-family:"Barlow Semi Condensed",sans-serif;font-weight:600;fill:#fff}
.footer{fill:var(--magenta)}
</style>
</head>
<body>
<main class="deck">

<!-- Cover -->
<section class="slide col-1 row-1" aria-label="Cover">
<svg viewBox="0 0 460 258">
<defs><linearGradient id="coverTint" x1="0" y1="0" x2="1" y2="1"><stop offset="0" stop-color="#b51a62"/><stop offset="1" stop-color="#8f1048"/></linearGradient></defs>
<rect width="460" height="258" fill="url(#coverTint)" role="img" aria-label="Photo of a presenter in a classroom, tinted magenta"/>
<text x="230" y="118" text-anchor="middle" font-family="Barlow Semi Condensed,sans-serif" font-weight="700" font-size="42" fill="#f7a21b">K7V</text>
<text x="230" y="175" text-anchor="middle" font-family="Barlow Semi Condensed,sans-serif" font-weight="600" font-size="19" fill="#fff">Investor Deck</text>
<text x="230" y="196" text-anchor="middle" font-family="Barlow,sans-serif" font-size="10" fill="#fff">Subtitle</text>
</svg>
</section>

<!-- Problems -->
<section class="slide col-2 row-1" aria-label="Problems">
<svg viewBox="0 0 460 258">
<text class="title" x="22" y="32">Problems</text>
<text class="fine" x="24" y="50">Short overview of the core problems our learners and partners face in reaching steady careers today.</text>
<text class="fine" x="24" y="56">Each point is outlined below in brief.</text>
<g id="prob">
<circle cx="36" cy="111" r="15" fill="var(--yellow)"/>
<rect x="48" y="86" width="110" height="49" rx="6" fill="var(--navy)"/>
<text class="head-sm" x="53" y="98">Heading</text>
<text class="fine-w" x="53" y="106">Short note on this problem</text>
<text class="fine-w" x="53" y="112">and the gap it leaves for</text>
<text class="fine-w" x="53" y="118">learners and employers.</text>
<text class="fine-w" x="53" y="124">Detail to follow.</text>
</g>
<use href="#prob" x="140"/><use href="#prob" x="283"/>
<use href="#prob" x="62" y="74"/><use href="#prob" x="217" y="74"/>
<rect class="footer" y="244" width="460" height="14"/><text class="brand" x="24" y="254">K7V</text>
</svg>
</section>

<!-- Solution -->
<section class="slide col-3 row-1" aria-label="Solution">
<svg viewBox="0 0 460 258">
<text class="title" x="22" y="32">Solution</text>
<g id="sol">
<circle cx="28" cy="54" r="3.5" fill="var(--orange)"/>
<text class="head-sm" x="35" y="57" style="fill:var(--orange)">Enter Title Here</text>
<text class="fine" x="35" y="64">Brief line describing how this part of the solution answers the stated problem.</text>
<text class="fine" x="35" y="69">Second line with a short supporting detail.</text>
</g>
<g transform="translate(0,30)"><circle cx="28" cy="54" r="3.5" fill="var(--teal)"/><text class="head-sm" x="35" y="57" style="fill:var(--teal)">Enter Title Here</text><text class="fine" x="35" y="64">Brief line describing how this part of the solution answers the stated problem.</text><text class="fine" x="35" y="69">Second line with a short supporting detail.</text></g>
<g transform="translate(0,60)"><circle cx="28" cy="54" r="3.5" fill="var(--blue)"/><text class="head-sm" x="35" y="57" style="fill:var(--blue)">Enter Title Here</text><text class="fine" x="35" y="64">Brief line describing how this part of the solution answers the stated problem.</text><text class="fine" x="35" y="69">Second line with a short supporting detail.</text></g>
<g transform="translate(0,90)"><circle cx="28" cy="54" r="3.5" fill="var(--magenta)"/><text class="head-sm" x="35" y="57" style="fill:var(--magenta)">Enter Title Here</text><text class="fine" x="35" y="64">Brief line describing how this part of the solution answers the stated problem.</text><text class="fine" x="35" y="69">Second line with a short supporting detail.</text></g>
<g transform="translate(0,120)"><circle cx="28" cy="54" r="3.5" fill="var(--navy)"/><text class="head-sm" x="35" y="57" style="fill:var(--navy)">Enter Title Here</text><text class="fine" x="35" y="64">Brief line describing how this part of the solution answers the stated problem.</text><text class="fine" x="35" y="69">Second line with a short supporting detail.</text></g>
<g transform="translate(0,150)"><circle cx="28" cy="54" r="3.5" fill="var(--yellow)"/><text class="head-sm" x="35" y="57" style="fill:var(--ochre)">Enter Title Here</text><text class="fine" x="35" y="64">Brief line describing how this part of the solution answers the stated problem.</text><text class="fine" x="35" y="69">Second line with a short supporting detail.</text></g>
<defs><radialGradient id="bulb" cx=".5" cy=".4" r=".6"><stop offset="0" stop-color="#fbd76a"/><stop offset="1" stop-color="#fff6da"/></radialGradient></defs>
<rect x="272" y="88" width="160" height="118" rx="50" fill="url(#bulb)" role="img" aria-label="Illustration of two people assembling a light bulb from puzzle pieces"/>
<rect class="footer" y="244" width="460" height="14"/><text class="brand" x="24" y="254">K7V</text>
</svg>
</section>

<!-- Company Introduction -->
<section class="slide col-1 row-2" aria-label="Company Introduction">
<svg viewBox="0 0 460 258">
<text class="title" x="22" y="32">Company Introduction</text>
<text class="fine" x="24" y="50">Short introduction to the company, who we serve and why our approach to career pathways stands apart in the market.</text>
<text class="fine" x="24" y="56">A second line with one closing point.</text>
<text class="head-sm" x="24" y="80">Our Vision</text>
<path d="M24 89 q13 7 26 0" stroke="var(--teal)" stroke-width="2" fill="none"/>
<text class="fine" x="24" y="108">Short statement of where</text><text class="fine" x="24" y="114">we aim to be in the coming</text><text class="fine" x="24" y="120">years and the change we</text><text class="fine" x="24" y="126">hope to bring to learners</text><text class="fine" x="24" y="132">and their communities.</text>
<text class="head-sm" x="137" y="80">Our Vision</text>
<path d="M137 89 q13 7 26 0" stroke="var(--yellow)" stroke-width="2" fill="none"/>
<text class="fine" x="137" y="108">Short statement of where</text><text class="fine" x="137" y="114">we aim to be in the coming</text><text class="fine" x="137" y="120">years and the change we</text><text class="fine" x="137" y="126">hope to bring to learners</text><text class="fine" x="137" y="132">and their communities.</text>
<text class="head-sm" x="263" y="80">Our Values</text>
<path d="M263 89 q13 7 26 0" stroke="var(--orange)" stroke-width="2" fill="none"/>
<text class="head-sm" x="263" y="110" style="fill:var(--ink)">Heading</text><text class="fine" x="263" y="117">One value described in a short line of supporting text here.</text><text class="fine" x="263" y="123">A second short line.</text>
<text class="head-sm" x="263" y="154" style="fill:var(--ink)">Heading</text><text class="fine" x="263" y="161">One value described in a short line of supporting text here.</text><text class="fine" x="263" y="167">A second short line.</text>
<text class="head-sm" x="263" y="198" style="fill:var(--ink)">Heading</text><text class="fine" x="263" y="205">One value described in a short line of supporting text here.</text><text class="fine" x="263" y="211">A second short line.</text>
<rect x="24" y="175" width="202" height="60" fill="#b9a28c" role="img" aria-label="Photo of a smiling student in a hallway"/>
<rect class="footer" y="244" width="460" height="14"/><text class="brand" x="24" y="254">K7V</text>
</svg>
</section>

<!-- Our Services (photos) -->
<section class="slide col-2 row-2" aria-label="Our Services">
<svg viewBox="0 0 460 258">
<text class="title" x="22" y="32">Our Services</text>
<text class="fine" x="24" y="50">Short overview of the services we offer to learners, schools and employers across every stage of the career pathway.</text>
<text class="fine" x="24" y="56">Details for each service are below.</text>
<g id="svc">
<rect x="22" y="72" width="74" height="50" fill="#9aa3a8" role="img" aria-label="Photo for a service"/>
<text class="head-sm" x="22" y="134">Heading</text>
<text class="fine" x="22" y="141">Brief text describing this</text><text class="fine" x="22" y="146">service and what it offers</text><text class="fine" x="22" y="151">to those who take part in</text><text class="fine" x="22" y="156">it over the year.</text>
<text class="fine" x="22" y="168">A further note on scope</text><text class="fine" x="22" y="173">and delivery.</text>
<text class="fine" x="22" y="185">Closing line on results</text><text class="fine" x="22" y="190">and outcomes.</text>
</g>
<use href="#svc" x="86"/><use href="#svc" x="172"/><use href="#svc" x="258"/><use href="#svc" x="344"/>
<rect class="footer" y="244" width="460" height="14"/><text class="brand" x="24" y="254">K7V</text>
</svg>
</section>

<!-- Our Services (petals) -->
<section class="slide col-3 row-2" aria-label="Our Services">
<svg viewBox="0 0 460 258">
<text class="title" x="22" y="32">Our Services</text>
<g id="svl"><text class="head-sm" x="38" y="78">Heading</text><text class="fine" x="38" y="85">Brief line on this service and the people it</text><text class="fine" x="38" y="90">supports, with one short closing note.</text><text class="fine" x="38" y="95">Key result noted here.</text></g>
<use href="#svl" y="55"/><use href="#svl" y="105"/>
<use href="#svl" x="267"/><use href="#svl" x="267" y="55"/><use href="#svl" x="267" y="105"/>
<circle cx="230" cy="100" r="20" fill="var(--magenta)"/><circle cx="268" cy="114" r="20" fill="var(--teal)"/>
<circle cx="284" cy="150" r="20" fill="var(--blue)"/><circle cx="268" cy="186" r="20" fill="var(--orange)"/>
<circle cx="230" cy="200" r="20" fill="var(--yellow)"/><circle cx="192" cy="186" r="20" fill="var(--yellow)"/>
<circle cx="176" cy="150" r="20" fill="var(--navy)"/><circle cx="192" cy="114" r="20" fill="var(--teal)"/>
<circle cx="230" cy="150" r="40" fill="#fff"/>
<circle cx="230" cy="150" r="35" fill="#c9a76f" role="img" aria-label="Photo of a teacher at the front of a class"/>
<rect class="footer" y="244" width="460" height="14"/><text class="brand" x="24" y="254">K7V</text>
</svg>
</section>

<!-- Management Team -->
<section class="slide col-1 row-3" aria-label="Management Team">
<svg viewBox="0 0 460 258">
<text class="title" x="22" y="32">Management Team</text>
<g id="mgr">
<circle cx="40" cy="72" r="16" fill="#cfe8e6" role="img" aria-label="Avatar illustration of a team member"/>
<text class="head-sm" x="62" y="62" style="fill:var(--orange)">Name:</text>
<text class="head-sm" x="62" y="70" style="fill:var(--ink)">Designation:</text>
<text class="fine" x="62" y="83" style="fill:var(--muted)">Short profile line on this person, their role and past work in the sector.</text>
<text class="fine" x="62" y="88" style="fill:var(--muted)">Key skills and one closing note on focus areas.</text>
<text class="fine" x="62" y="99" style="fill:var(--muted)">Prior roles listed in brief.</text>
<text class="fine" x="62" y="111" style="fill:var(--muted)">Education and credentials noted here.</text>
</g>
<use href="#mgr" x="224"/><use href="#mgr" y="96"/><use href="#mgr" x="224" y="96"/>
<rect class="footer" y="244" width="460" height="14"/><text class="brand" x="24" y="254">K7V</text>
</svg>
</section>

<!-- Fund raise -->
<section class="slide col-2 row-3" aria-label="Fund raise">
<svg viewBox="0 0 460 258">
<rect x="202" y="0" width="258" height="244" fill="var(--panel)"/>
<text class="title" x="22" y="32">Fund raise</text>
<text class="head" x="22" y="90">Heading</text>
<text class="copy" x="22" y="101">Short summary of the raise, the amount sought,</text>
<text class="copy" x="22" y="109">and how the funds will be used across the</text>
<text class="copy" x="22" y="117">business over the next stage of growth and</text>
<text class="copy" x="22" y="125">delivery.</text>
<text class="copy" x="22" y="140">A short note on timing and terms.</text>
<text class="copy" x="22" y="148">Further detail.</text>
<text class="copy" x="22" y="163">Closing line on expected results</text>
<text class="copy" x="22" y="171">and milestones.</text>
<text x="325" y="40" text-anchor="middle" font-family="Barlow,sans-serif" font-weight="600" font-size="7" fill="var(--ink)">SALES</text>
<g class="label"><rect x="279" y="49" width="4" height="4" fill="var(--orange)"/><text x="285" y="53">1st Qtr</text><rect x="304" y="49" width="4" height="4" fill="var(--blue)"/><text x="310" y="53">2nd Qtr</text><rect x="330" y="49" width="4" height="4" fill="var(--teal)"/><text x="336" y="53">3rd Qtr</text><rect x="355" y="49" width="4" height="4" fill="var(--magenta)"/><text x="361" y="53">4th Qtr</text></g>
<g transform="rotate(-90 325 120)" fill="none" stroke-width="26">
<circle cx="325" cy="120" r="47" stroke="var(--orange)" stroke-dasharray="171.3 295.3"/>
<circle cx="325" cy="120" r="47" stroke="var(--teal)" stroke-dasharray="67.9 295.3" stroke-dashoffset="-171.3"/>
<circle cx="325" cy="120" r="47" stroke="var(--blue)" stroke-dasharray="29.5 295.3" stroke-dashoffset="-239.2"/>
<circle cx="325" cy="120" r="47" stroke="var(--magenta)" stroke-dasharray="26.6 295.3" stroke-dashoffset="-268.7"/>
</g>
<g class="num" font-size="9"><text x="373" y="123">58%</text><text x="280" y="126">23%</text><text x="288" y="97">10%</text><text x="314" y="80">9%</text></g>
<rect class="footer" y="244" width="460" height="14"/><text class="brand" x="24" y="254">K7V</text>
</svg>
</section>

<!-- Financial overview -->
<section class="slide col-3 row-3" aria-label="Financial overview">
<svg viewBox="0 0 460 258">
<rect x="202" y="0" width="258" height="244" fill="var(--panel)"/>
<text class="title" x="22" y="32">Financia overview</text>
<text class="head" x="22" y="90">Heading</text>
<text class="copy" x="22" y="101">Short summary of revenue, costs and margins,</text>
<text class="copy" x="22" y="109">with the main trends seen over the last few</text>
<text class="copy" x="22" y="117">periods and what drives them across the</text>
<text class="copy" x="22" y="125">business.</text>
<text class="copy" x="22" y="140">A short note on the outlook.</text>
<text class="copy" x="22" y="148">Further detail.</text>
<text class="copy" x="22" y="163">Closing line on targets for the</text>
<text class="copy" x="22" y="171">coming year.</text>
<text x="326" y="72" text-anchor="middle" font-family="Barlow,sans-serif" font-weight="600" font-size="7" fill="var(--ink)">Chart Title</text>
<g stroke="#ddd" stroke-width=".5"><line x1="232" y1="80" x2="435" y2="80"/><line x1="232" y1="95" x2="435" y2="95"/><line x1="232" y1="110" x2="435" y2="110"/><line x1="232" y1="125" x2="435" y2="125"/><line x1="232" y1="140" x2="435" y2="140"/><line x1="232" y1="155" x2="435" y2="155"/><line x1="232" y1="170" x2="435" y2="170"/></g>
<g class="label" text-anchor="end"><text x="228" y="82">6</text><text x="228" y="97">5</text><text x="228" y="112">4</text><text x="228" y="127">3</text><text x="228" y="142">2</text><text x="228" y="157">1</text><text x="228" y="172">0</text></g>
<g fill="var(--orange)"><rect x="242" y="105.5" width="8" height="64.5"/><rect x="297" y="132.5" width="8" height="37.5"/><rect x="352" y="117.5" width="8" height="52.5"/><rect x="407" y="102.5" width="8" height="67.5"/></g>
<g fill="var(--teal)"><rect x="251" y="134" width="8" height="36"/><rect x="306" y="104" width="8" height="66"/><rect x="361" y="143" width="8" height="27"/><rect x="416" y="128" width="8" height="42"/></g>
<g fill="var(--blue)"><rect x="260" y="140" width="8" height="30"/><rect x="315" y="140" width="8" height="30"/><rect x="370" y="125" width="8" height="45"/><rect x="425" y="95" width="8" height="75"/></g>
<g class="label" text-anchor="middle"><text x="255" y="180">Category 1</text><text x="310" y="180">Category 2</text><text x="365" y="180">Category 3</text><text x="420" y="180">Category 4</text></g>
<g class="label"><rect x="300" y="185" width="4" height="4" fill="var(--orange)"/><text x="306" y="189">Series 1</text><rect x="325" y="185" width="4" height="4" fill="var(--teal)"/><text x="331" y="189">Series 2</text><rect x="350" y="185" width="4" height="4" fill="var(--blue)"/><text x="356" y="189">Series 3</text></g>
<rect class="footer" y="244" width="460" height="14"/><text class="brand" x="24" y="254">K7V</text>
</svg>
</section>

<!-- Growth Roadmap -->
<section class="slide col-1 row-4" aria-label="Growth Roadmap">
<svg viewBox="0 0 460 258">
<rect x="0" y="0" width="230" height="244" fill="var(--mint)"/>
<rect x="230" y="0" width="230" height="244" fill="var(--cream)"/>
<text class="title" x="230" y="32" text-anchor="middle">Growth Roadmap</text>
<text x="22" y="76" font-family="Barlow Semi Condensed,sans-serif" font-weight="700" font-size="8" fill="var(--ink)">PHASE I</text>
<text class="head" x="22" y="92">Heading</text>
<text class="copy" x="22" y="103">Short summary of goals for this phase,</text><text class="copy" x="22" y="111">the markets we enter and the key steps</text><text class="copy" x="22" y="119">taken to grow our learner base in the</text><text class="copy" x="22" y="127">first year of work.</text>
<text class="copy" x="22" y="142">A short note on budget and team.</text><text class="copy" x="22" y="150">Further detail.</text>
<text class="copy" x="22" y="170">Closing line on the expected result</text><text class="copy" x="22" y="178">of this phase.</text>
<path d="M0 222 H186 a14 14 0 0 0 14 -14 V100" fill="none" stroke="var(--teal)" stroke-width="20"/>
<path d="M182 104 L200 80 L218 104 Z" fill="var(--teal)"/>
<text x="300" y="76" font-family="Barlow Semi Condensed,sans-serif" font-weight="700" font-size="8" fill="var(--ink)">PHASE II</text>
<text class="head" x="300" y="92">Heading</text>
<text class="copy" x="300" y="103">Short summary of goals for this phase,</text><text class="copy" x="300" y="111">the markets we enter and the key steps</text><text class="copy" x="300" y="119">taken to grow our learner base in the</text><text class="copy" x="300" y="127">second year of work.</text>
<text class="copy" x="300" y="142">A short note on budget and team.</text><text class="copy" x="300" y="150">Further detail.</text>
<text class="copy" x="300" y="170">Closing line on the expected result</text><text class="copy" x="300" y="178">of this phase.</text>
<path d="M460 222 H274 a14 14 0 0 1 -14 -14 V100" fill="none" stroke="var(--yellow)" stroke-width="20"/>
<path d="M242 104 L260 80 L278 104 Z" fill="var(--yellow)"/>
<rect class="footer" y="244" width="460" height="14"/><text class="brand" x="24" y="254">K7V</text>
</svg>
</section>

<!-- Milestones -->
<section class="slide col-2 row-4" aria-label="Milestones">
<svg viewBox="0 0 460 258">
<text class="title" x="22" y="32">Milestones</text>
<line x1="0" y1="137" x2="460" y2="137" stroke="#f3d98a" stroke-width="1.5"/>
<g id="mst">
<rect x="33" y="52" width="44" height="64" rx="2" fill="#eeeeee"/>
<rect x="33" y="52" width="44" height="6" fill="var(--navy)"/>
<text x="55" y="57" text-anchor="middle" font-family="Barlow,sans-serif" font-weight="600" font-size="4.5" fill="#fff">Year</text>
<text class="fine" x="36" y="65" style="fill:var(--teal);font-weight:600">Heading</text>
<text class="fine" x="36" y="71">Short note on</text><text class="fine" x="36" y="76">what was done</text><text class="fine" x="36" y="81">in this year</text><text class="fine" x="36" y="86">and the result</text><text class="fine" x="36" y="91">it brought to</text><text class="fine" x="36" y="96">the business.</text>
<line x1="55" y1="116" x2="55" y2="134" stroke="#bbb" stroke-width=".5"/>
</g>
<use href="#mst" x="86"/><use href="#mst" x="172"/><use href="#mst" x="258"/><use href="#mst" x="345"/>
<g id="msb">
<rect x="76" y="158" width="44" height="64" rx="2" fill="#eeeeee"/>
<rect x="76" y="216" width="44" height="6" fill="var(--navy)"/>
<text x="98" y="221" text-anchor="middle" font-family="Barlow,sans-serif" font-weight="600" font-size="4.5" fill="#fff">Year</text>
<text class="fine" x="79" y="166" style="fill:var(--teal);font-weight:600">Heading</text>
<text class="fine" x="79" y="172">Short note on</text><text class="fine" x="79" y="177">what was done</text><text class="fine" x="79" y="182">in this year</text><text class="fine" x="79" y="187">and the result</text><text class="fine" x="79" y="192">it brought to</text><text class="fine" x="79" y="197">the business.</text>
<line x1="98" y1="140" x2="98" y2="158" stroke="#bbb" stroke-width=".5"/>
</g>
<use href="#msb" x="86"/><use href="#msb" x="172"/><use href="#msb" x="258"/>
<g fill="var(--teal)" stroke="#fff" stroke-width="1"><circle cx="55" cy="137" r="4"/><circle cx="98" cy="137" r="4"/><circle cx="141" cy="137" r="4"/><circle cx="184" cy="137" r="4"/><circle cx="227" cy="137" r="4"/><circle cx="270" cy="137" r="4"/><circle cx="313" cy="137" r="4"/><circle cx="356" cy="137" r="4"/><circle cx="400" cy="137" r="4"/></g>
<rect class="footer" y="244" width="460" height="14"/><text class="brand" x="24" y="254">K7V</text>
</svg>
</section>

<!-- Our Traction (images) -->
<section class="slide col-3 row-4" aria-label="Our Traction">
<svg viewBox="0 0 460 258">
<text class="title" x="22" y="32">Our Traction</text>
<g font-family="Barlow,sans-serif" font-size="7" fill="#9a9a9a" text-anchor="middle">
<rect x="22" y="50" width="120" height="80" fill="#dcdcdc" role="img" aria-label="Image placeholder"/><text x="82" y="93">Image</text>
<rect x="237" y="50" width="120" height="80" fill="#dcdcdc" role="img" aria-label="Image placeholder"/><text x="297" y="93">Image</text>
<rect x="22" y="141" width="120" height="80" fill="#dcdcdc" role="img" aria-label="Image placeholder"/><text x="82" y="184">Image</text>
<rect x="237" y="141" width="120" height="80" fill="#dcdcdc" role="img" aria-label="Image placeholder"/><text x="297" y="184">Image</text>
</g>
<g id="trc"><rect x="142" y="50" width="72" height="80" fill="var(--teal)"/>
<text class="fine-w" x="146" y="71" style="font-weight:600">Heading</text>
<text class="fine-w" x="146" y="77">Short note on growth</text><text class="fine-w" x="146" y="82">seen in this area with</text><text class="fine-w" x="146" y="87">one key figure and a</text><text class="fine-w" x="146" y="92">brief line of context</text><text class="fine-w" x="146" y="97">for the reader.</text></g>
<use href="#trc" x="215" style="--c:1"/>
<rect x="357" y="50" width="72" height="80" fill="var(--magenta)"/>
<text class="fine-w" x="361" y="71" style="font-weight:600">Heading</text><text class="fine-w" x="361" y="77">Short note on growth</text><text class="fine-w" x="361" y="82">seen in this area with</text><text class="fine-w" x="361" y="87">one key figure and a</text><text class="fine-w" x="361" y="92">brief line of context</text><text class="fine-w" x="361" y="97">for the reader.</text>
<rect x="142" y="141" width="72" height="80" fill="var(--blue)"/>
<text class="fine-w" x="146" y="162" style="font-weight:600">Heading</text><text class="fine-w" x="146" y="168">Short note on growth</text><text class="fine-w" x="146" y="173">seen in this area with</text><text class="fine-w" x="146" y="178">one key figure and a</text><text class="fine-w" x="146" y="183">brief line of context</text><text class="fine-w" x="146" y="188">for the reader.</text>
<rect x="357" y="141" width="72" height="80" fill="var(--ochre)"/>
<text class="fine-w" x="361" y="162" style="font-weight:600">Heading</text><text class="fine-w" x="361" y="168">Short note on growth</text><text class="fine-w" x="361" y="173">seen in this area with</text><text class="fine-w" x="361" y="178">one key figure and a</text><text class="fine-w" x="361" y="183">brief line of context</text><text class="fine-w" x="361" y="188">for the reader.</text>
<rect class="footer" y="244" width="460" height="14"/><text class="brand" x="24" y="254">K7V</text>
</svg>
</section>

<!-- Our Traction (stats) -->
<section class="slide col-1 row-5" aria-label="Our Traction">
<svg viewBox="0 0 460 258">
<text class="title" x="22" y="32">Our Traction</text>
<g id="stat">
<rect x="23" y="47" width="98" height="83" fill="var(--teal)"/>
<text class="num" x="72" y="86" font-size="32" text-anchor="middle">123</text>
<g font-family="Barlow,sans-serif" font-size="5.4" fill="#fff" text-anchor="middle"><text x="72" y="100">Short line on what this</text><text x="72" y="107">number measures for the</text><text x="72" y="114">business this past</text><text x="72" y="121">year.</text></g>
</g>
<use href="#stat" x="107"/><use href="#stat" y="97"/><use href="#stat" x="107" y="97"/>
<text x="343" y="56" text-anchor="middle" font-family="Barlow,sans-serif" font-size="7" fill="#666">Chart Title</text>
<g stroke="#ddd" stroke-width=".5"><line x1="265" y1="63" x2="430" y2="63"/><line x1="265" y1="83" x2="430" y2="83"/><line x1="265" y1="103" x2="430" y2="103"/><line x1="265" y1="123" x2="430" y2="123"/><line x1="265" y1="143" x2="430" y2="143"/><line x1="265" y1="163" x2="430" y2="163"/><line x1="265" y1="183" x2="430" y2="183"/><line x1="265" y1="203" x2="430" y2="203"/></g>
<g class="label" text-anchor="end"><text x="261" y="65">14</text><text x="261" y="85">12</text><text x="261" y="105">10</text><text x="261" y="125">8</text><text x="261" y="145">6</text><text x="261" y="165">4</text><text x="261" y="185">2</text><text x="261" y="205">0</text></g>
<g fill="var(--yellow)"><rect x="276" y="160" width="15" height="43"/><rect x="318" y="178" width="15" height="25"/><rect x="360" y="168" width="15" height="35"/><rect x="401" y="158" width="15" height="45"/></g>
<g fill="var(--navy)"><rect x="276" y="136" width="15" height="24"/><rect x="318" y="113" width="15" height="65"/><rect x="360" y="150" width="15" height="18"/><rect x="401" y="130" width="15" height="28"/></g>
<g fill="var(--blue)"><rect x="276" y="116" width="15" height="20"/><rect x="318" y="113" width="15" height="0"/><rect x="318" y="93" width="15" height="20"/><rect x="360" y="120" width="15" height="30"/><rect x="401" y="80" width="15" height="50"/></g>
<g class="label" text-anchor="middle"><text x="284" y="213">Category 1</text><text x="325" y="213">Category 2</text><text x="367" y="213">Category 3</text><text x="408" y="213">Category 4</text></g>
<g class="label"><rect x="308" y="218" width="4" height="4" fill="var(--yellow)"/><text x="314" y="222">Series 1</text><rect x="333" y="218" width="4" height="4" fill="var(--navy)"/><text x="339" y="222">Series 2</text><rect x="358" y="218" width="4" height="4" fill="var(--blue)"/><text x="364" y="222">Series 3</text></g>
<rect class="footer" y="244" width="460" height="14"/><text class="brand" x="24" y="254">K7V</text>
</svg>
</section>

<!-- Go-To-Market Strategy -->
<section class="slide col-2 row-5" aria-label="Go-To-Market Strategy">
<svg viewBox="0 0 460 258">
<text class="title" x="22" y="32">Go-To-Market Strategy</text>
<g id="gtm">
<path d="M40 126 q15 9 30 0" stroke="var(--teal)" stroke-width="2" fill="none"/>
<line x1="55" y1="138" x2="55" y2="150" stroke="#999" stroke-width=".6"/>
<text class="head-sm" x="55" y="173" text-anchor="middle">Heading</text>
<g class="fine" text-anchor="middle"><text x="55" y="180">Short note on this channel</text><text x="55" y="185">and how we reach people</text><text x="55" y="190">through partners, schools</text><text x="55" y="195">and local groups in the</text><text x="55" y="200">first markets.</text></g>
</g>
<use href="#gtm" x="87"/><use href="#gtm" x="173"/><use href="#gtm" x="260"/><use href="#gtm" x="347"/>
<circle cx="55" cy="89" r="33" fill="var(--teal)"/><circle cx="142" cy="89" r="33" fill="var(--orange)"/><circle cx="228" cy="89" r="33" fill="var(--blue)"/><circle cx="315" cy="89" r="33" fill="var(--magenta)"/><circle cx="402" cy="89" r="33" fill="var(--yellow)"/>
<rect class="footer" y="244" width="460" height="14"/><text class="brand" x="24" y="254">K7V</text>
</svg>
</section>

<!-- Competitive Advantage -->
<section class="slide col-3 row-5" aria-label="Competitive Advantage">
<svg viewBox="0 0 460 258">
<text class="title" x="22" y="32">Competitive Advantage</text>
<rect x="22" y="65" width="153" height="140" fill="#9fb1bf" role="img" aria-label="Photo of a smiling student holding books"/>
<g id="adv">
<text class="head-sm" x="248" y="75">Heading</text>
<text class="fine" x="248" y="83">Short line on one advantage we hold over others in the market, with a note on</text>
<text class="fine" x="248" y="88">why it matters to learners and how it helps us grow with partners and employers.</text>
<text class="fine" x="248" y="93">Closing remark on the result so far.</text>
</g>
<use href="#adv" y="53"/><use href="#adv" y="106"/>
<circle cx="226" cy="76" r="17" fill="var(--orange)"/><circle cx="226" cy="129" r="17" fill="var(--teal)"/><circle cx="226" cy="182" r="17" fill="var(--yellow)"/>
<rect class="footer" y="244" width="460" height="14"/><text class="brand" x="24" y="254">K7V</text>
</svg>
</section>

<!-- Competitive Analysis -->
<section class="slide col-1 row-6" aria-label="Competitive Analysis">
<svg viewBox="0 0 460 258">
<text class="title" x="22" y="32">Competitive Analysis</text>
<g id="cmp">
<g class="label" text-anchor="middle">
<rect x="31" y="110" width="48" height="26" rx="3" fill="#fff"/><text x="55" y="124">Logo here</text>
<rect x="88" y="110" width="48" height="26" rx="3" fill="#fff"/><text x="112" y="124">Logo here</text>
<rect x="31" y="146" width="48" height="26" rx="3" fill="#fff"/><text x="55" y="160">Logo here</text>
<rect x="88" y="146" width="48" height="26" rx="3" fill="#fff"/><text x="112" y="160">Logo here</text>
<rect x="31" y="182" width="48" height="26" rx="3" fill="#fff"/><text x="55" y="196">Logo here</text>
<rect x="88" y="182" width="48" height="26" rx="3" fill="#fff"/><text x="112" y="196">Logo here</text>
</g>
<g class="fine" text-anchor="middle"><text x="84" y="73">Short line on this group</text><text x="84" y="78">of rival providers.</text></g>
</g>
<rect x="22" y="46" width="128" height="182" rx="8" fill="var(--peach)"/>
<rect x="164" y="46" width="128" height="182" rx="8" fill="var(--mint)"/>
<rect x="306" y="46" width="128" height="182" rx="8" fill="var(--cream)"/>
<use href="#cmp" x="-2"/><use href="#cmp" x="140"/><use href="#cmp" x="282"/>
<text class="head-sm" x="86" y="65" text-anchor="middle" style="fill:var(--orange)">Heading</text>
<text class="head-sm" x="228" y="65" text-anchor="middle">Heading</text>
<text class="head-sm" x="370" y="65" text-anchor="middle" style="fill:var(--orange)">Heading</text>
<path d="M74 88 q12 6 24 0" stroke="var(--orange)" stroke-width="2" fill="none"/>
<path d="M216 88 q12 6 24 0" stroke="var(--teal)" stroke-width="2" fill="none"/>
<path d="M358 88 q12 6 24 0" stroke="var(--yellow)" stroke-width="2" fill="none"/>
<rect class="footer" y="244" width="460" height="14"/><text class="brand" x="24" y="254">K7V</text>
</svg>
</section>

<!-- Target Markets -->
<section class="slide col-2 row-6" aria-label="Target Markets">
<svg viewBox="0 0 460 258">
<rect x="172" y="0" width="288" height="244" fill="var(--panel)"/>
<text class="title" x="22" y="32">Target Markets</text>
<text class="head" x="22" y="78">Heading</text>
<text class="copy" x="22" y="89">Short summary of the regions and groups we</text><text class="copy" x="22" y="97">serve first, with the size of each market</text><text class="copy" x="22" y="105">and why we chose them for the launch of</text><text class="copy" x="22" y="113">our career pathway work.</text>
<text class="copy" x="22" y="128">A short note on later regions.</text><text class="copy" x="22" y="136">Further detail.</text>
<text class="copy" x="22" y="152">Closing line on growth in each</text><text class="copy" x="22" y="160">market.</text>
<defs><linearGradient id="mapTone" x1="0" y1="0" x2="1" y2="0"><stop offset="0" stop-color="#9fd9d3"/><stop offset=".45" stop-color="#c9c9c9"/><stop offset="1" stop-color="#bdbdbd"/></linearGradient></defs>
<rect x="182" y="55" width="270" height="135" rx="30" fill="url(#mapTone)" role="img" aria-label="World map with target regions highlighted in teal"/>
<rect class="footer" y="244" width="460" height="14"/><text class="brand" x="24" y="254">K7V</text>
</svg>
</section>

<!-- Our Business Segments -->
<section class="slide col-3 row-6" aria-label="Our Business Segments">
<svg viewBox="0 0 460 258">
<text class="title" x="22" y="32">Our Business Segments</text>
<g id="segl"><text class="head-sm" x="22" y="58">Heading</text><text class="fine" x="22" y="65">Short note on this segment and</text><text class="fine" x="22" y="70">the revenue it brings in, with</text><text class="fine" x="22" y="75">one line on growth and one</text><text class="fine" x="22" y="80">on next steps.</text></g>
<use href="#segl" y="60"/><use href="#segl" y="118"/>
<g id="segr" text-anchor="end"><text class="head-sm" x="436" y="58">Heading</text><text class="fine" x="436" y="65">Short note on this segment and</text><text class="fine" x="436" y="70">the revenue it brings in, with</text><text class="fine" x="436" y="75">one line on growth and one</text><text class="fine" x="436" y="80">on next steps.</text></g>
<use href="#segr" y="60"/><use href="#segr" y="118"/>
<g stroke="#ccc" stroke-width=".5"><line x1="118" y1="75" x2="170" y2="75"/><line x1="118" y1="133" x2="160" y2="133"/><line x1="118" y1="190" x2="150" y2="190"/><line x1="340" y1="75" x2="290" y2="75"/><line x1="340" y1="133" x2="300" y2="133"/><line x1="340" y1="190" x2="310" y2="190"/></g>
<circle cx="230" cy="190" r="88" fill="var(--navy)"/>
<circle cx="230" cy="190" r="60" fill="var(--teal)"/>
<circle cx="230" cy="190" r="46" fill="#fff"/>
<circle cx="230" cy="190" r="40" fill="#c89a5a" role="img" aria-label="Photo of two students working together"/>
<g font-family="Barlow Semi Condensed,sans-serif" font-weight="700" font-size="9" text-anchor="middle">
<circle cx="160" cy="187" r="10" fill="var(--yellow)"/><text x="160" y="190" fill="#fff">1</text>
<circle cx="173" cy="147" r="10" fill="var(--blue)"/><text x="173" y="150" fill="#fff">2</text>
<circle cx="207" cy="122" r="10" fill="var(--magenta)"/><text x="207" y="125" fill="#fff">3</text>
<circle cx="251" cy="122" r="10" fill="#27545c"/><text x="251" y="125" fill="#fff">4</text>
<circle cx="285" cy="147" r="10" fill="var(--orange)"/><text x="285" y="150" fill="#fff">5</text>
<circle cx="298" cy="187" r="10" fill="#fff"/><text x="298" y="190" fill="var(--navy)">6</text>
</g>
<rect class="footer" y="244" width="460" height="14"/><text class="brand" x="24" y="254">K7V</text>
</svg>
</section>

<!-- Business Model -->
<section class="slide col-1 row-7" aria-label="Business Model">
<svg viewBox="0 0 460 258">
<text class="title" x="22" y="32">Business Model</text>
<g id="bm"><text class="head-sm" x="22" y="56">Heading</text><text class="fine" x="22" y="63">Short line on how this part of the model earns revenue, who pays and on</text><text class="fine" x="22" y="68">what terms, with a brief note on margin and</text><text class="fine" x="22" y="73">scale.</text></g>
<use href="#bm" y="48"/><use href="#bm" y="96"/><use href="#bm" y="144"/>
<text class="head-sm" x="22" y="104" style="fill:var(--ochre)">Heading</text>
<path d="M332 137 L332 48 A89 89 0 0 1 421 137 Z" fill="var(--teal)"/>
<path d="M332 137 L421 137 A89 89 0 0 1 332 226 Z" fill="var(--yellow)"/>
<path d="M332 137 L332 226 A89 89 0 0 1 243 137 Z" fill="var(--magenta)"/>
<path d="M332 137 L243 137 A89 89 0 0 1 332 48 Z" fill="var(--navy)"/>
<circle cx="332" cy="137" r="30" fill="var(--navy)" stroke="#fff" stroke-width="2"/>
<g class="fine-w" text-anchor="middle">
<text x="372" y="82">Short note on</text><text x="372" y="87">this stream of</text><text x="372" y="92">income.</text>
<text x="290" y="110">Short note on</text><text x="290" y="115">this stream of</text><text x="290" y="120">income.</text>
<text x="374" y="176">Short note on</text><text x="374" y="181">this stream of</text><text x="374" y="186">income.</text>
<text x="292" y="194">Short note on</text><text x="292" y="199">this stream of</text><text x="292" y="204">income.</text>
</g>
<rect class="footer" y="244" width="460" height="14"/><text class="brand" x="24" y="254">K7V</text>
</svg>
</section>

<!-- Market Opportunity -->
<section class="slide col-2 row-7" aria-label="Market Opportunity">
<svg viewBox="0 0 460 258">
<text class="title" x="22" y="32">Market Opportunity</text>
<g id="mo"><text class="head-sm" x="22" y="56">Heading</text><text class="fine" x="22" y="63">Short line on the size of this</text><text class="fine" x="22" y="68">part of the market and the</text><text class="fine" x="22" y="73">share we aim to reach within</text><text class="fine" x="22" y="78">the next few years.</text></g>
<use href="#mo" y="58"/><use href="#mo" y="116"/>
<g stroke="var(--orange)" stroke-width=".7"><line x1="125" y1="72" x2="185" y2="72"/><line x1="125" y1="130" x2="155" y2="130"/><line x1="105" y1="188" x2="130" y2="188"/></g>
<circle cx="263" cy="118" r="72" fill="var(--yellow)"/>
<circle cx="220" cy="140" r="46" fill="var(--teal)" stroke="#fff" stroke-width="2"/>
<circle cx="168" cy="188" r="35" fill="var(--blue)" stroke="#fff" stroke-width="2"/>
<g class="num" text-anchor="middle"><text x="263" y="92" font-size="22" font-weight="700">$123</text><text x="220" y="146" font-size="16" font-weight="400">$123</text><text x="168" y="194" font-size="16" font-weight="400">$123</text></g>
<text class="head" x="342" y="95">Heading</text>
<text class="copy" x="342" y="106">Short summary of the total</text><text class="copy" x="342" y="114">market, the part we can serve</text><text class="copy" x="342" y="122">and the share we plan to</text><text class="copy" x="342" y="130">win with our current model</text><text class="copy" x="342" y="138">and partners over</text><text class="copy" x="342" y="146">time.</text>
<rect class="footer" y="244" width="460" height="14"/><text class="brand" x="24" y="254">K7V</text>
</svg>
</section>

<!-- Project Fact Sheet -->
<section class="slide col-3 row-7" aria-label="Project Fact Sheet">
<svg viewBox="0 0 460 258">
<text class="title" x="22" y="32">Project Fact Sheet</text>
<g id="pfs">
<text class="fine" x="24" y="50">Short overview of the project, its scope, timeline and the partners involved in delivery across each site.</text>
<text class="fine" x="24" y="56">Key facts follow below.</text>
<g id="pfc"><text class="head-sm" x="24" y="104" style="fill:var(--ink)">Heading here</text>
<text class="fine" x="24" y="130">Short fact on this part</text><text class="fine" x="24" y="135">of the project, noting</text><text class="fine" x="24" y="140">the budget, dates and</text><text class="fine" x="24" y="145">the people who lead</text><text class="fine" x="24" y="150">the work and how it</text><text class="fine" x="24" y="155">is measured over</text><text class="fine" x="24" y="160">time.</text></g>
<use href="#pfc" x="85"/><use href="#pfc" x="169"/><use href="#pfc" x="254"/><use href="#pfc" x="338"/>
<path d="M24 114 q13 7 26 0" stroke="var(--teal)" stroke-width="2" fill="none"/>
<path d="M109 114 q13 7 26 0" stroke="var(--orange)" stroke-width="2" fill="none"/>
<path d="M193 114 q13 7 26 0" stroke="var(--blue)" stroke-width="2" fill="none"/>
<path d="M278 114 q13 7 26 0" stroke="var(--magenta)" stroke-width="2" fill="none"/>
<path d="M362 114 q13 7 26 0" stroke="var(--yellow)" stroke-width="2" fill="none"/>
</g>
<rect class="footer" y="244" width="460" height="14"/><text class="brand" x="24" y="254">K7V</text>
</svg>
</section>

<!-- Project Fact Sheet (second) -->
<section class="slide col-1 row-8" aria-label="Project Fact Sheet">
<svg viewBox="0 0 460 258">
<text class="title" x="22" y="32">Project Fact Sheet</text>
<text class="fine" x="24" y="50">Short overview of the project, its scope, timeline and the partners involved in delivery across each site.</text>
<text class="fine" x="24" y="56">Key facts follow below.</text>
<g id="pfc2"><text class="head-sm" x="24" y="104" style="fill:var(--ink)">Heading here</text>
<text class="fine" x="24" y="130">Short fact on this part</text><text class="fine" x="24" y="135">of the project, noting</text><text class="fine" x="24" y="140">the budget, dates and</text><text class="fine" x="24" y="145">the people who lead</text><text class="fine" x="24" y="150">the work and how it</text><text class="fine" x="24" y="155">is measured over</text><text class="fine" x="24" y="160">time.</text></g>
<use href="#pfc2" x="85"/><use href="#pfc2" x="169"/><use href="#pfc2" x="254"/><use href="#pfc2" x="338"/>
<path d="M24 114 q13 7 26 0" stroke="var(--teal)" stroke-width="2" fill="none"/>
<path d="M109 114 q13 7 26 0" stroke="var(--orange)" stroke-width="2" fill="none"/>
<path d="M193 114 q13 7 26 0" stroke="var(--blue)" stroke-width="2" fill="none"/>
<path d="M278 114 q13 7 26 0" stroke="var(--magenta)" stroke-width="2" fill="none"/>
<path d="M362 114 q13 7 26 0" stroke="var(--yellow)" stroke-width="2" fill="none"/>
<rect class="footer" y="244" width="460" height="14"/><text class="brand" x="24" y="254">K7V</text>
</svg>
</section>

</main>
</body>
</html>
```